Marlowe Crest Realty business card design

Looking for an upscale and clean business card design and updated logo. I sell to a very high-end south Florida real estate market.
Target Market(s)
High-end real estate in south Florida real estate market
Industry/Entity Type
Real Estate Agent
Contact Information for Business Card
Marlowe Crest Realty, Inc
738 West Pinecrest Ave, Suite 410/510, Fort Lauderdale, FL 33308
Gary Whitlock - Broker/Owner
954-327-8846 Direct
garyshomes@quellmail.com
Website: DwellTarrowBay.com
Font styles to use
Other font styles liked:
- Copperplate Gothic, Georgia, etc.
Requirements
Must have
- My photo, company name, my name and title, all info stated in Details above
Nice to have
- Luxury home design element, waterfront

```html
<!DOCTYPE html>
<html lang="en">
<head>
<meta charset="utf-8">
<title>Marlowe Crest Realty – Business Card</title>
<link href="https://fonts.googleapis.com/css2?family=EB+Garamond:wght@400&family=Michroma&family=Open+Sans:wght@400;600&display=swap" rel="stylesheet">
<style>
  :root {
    --stage: #2b2b2b;
    --paper: #ffffff;
    --ink: #1a1a1a;
    --night: #000000;
    --sun: #f4c433;
  }
  * { margin: 0; padding: 0; box-sizing: border-box; }
  html, body {
    width: 1200px; height: 976px; overflow: hidden;
    background: var(--stage);
  }
  .stage { position: relative; width: 1200px; height: 976px; }
  .card {
    position: absolute; left: 220px; width: 760px; height: 434px;
    overflow: hidden; box-shadow: 0 10px 30px rgba(0,0,0,.5);
  }
  .card-front { top: 42px; background: var(--paper); }
  .card-back { top: 500px; background: var(--night); }

  .brand {
    display: flex; align-items: center; gap: 16px;
    font-family: "EB Garamond", Georgia, serif; font-weight: 400;
    color: var(--ink); white-space: nowrap;
  }
  .brand-dot { border-radius: 50%; background: var(--sun); flex: none; }
  .card-front .brand {
    position: absolute; left: 50%; top: 50%;
    transform: translate(-50%, -50%); font-size: 40px;
  }
  .card-front .brand-dot { width: 46px; height: 46px; }

  .back-arc { position: absolute; inset: 0; }
  .card-back .brand {
    position: absolute; left: 478px; top: 198px; font-size: 22px; gap: 10px;
  }
  .card-back .brand-dot { width: 24px; height: 24px; }

  .person { position: absolute; left: 60px; top: 120px; }
  .person-name {
    font-family: "Michroma", "Arial Black", sans-serif;
    color: var(--sun); font-size: 16px; letter-spacing: 3px; white-space: nowrap;
  }
  .person-title {
    font-family: "Open Sans", Arial, sans-serif; color: var(--paper);
    font-size: 12px; margin-top: 3px;
  }
  .contacts {
    position: absolute; left: 60px; top: 220px; list-style: none;
    font-family: "Open Sans", Arial, sans-serif; color: var(--paper);
    font-size: 15px; line-height: 1.3;
  }
  .contacts li { display: flex; align-items: flex-start; gap: 12px; margin-bottom: 9px; white-space: nowrap; }
  .contacts svg { width: 20px; height: 20px; flex: none; fill: none; stroke: var(--paper); stroke-width: 1.6; }
</style>
</head>
<body>
<main class="stage">
  <section class="card card-front" aria-label="Card front">
    <div class="brand"><span class="brand-dot"></span><span>Marlowe Crest Realty, Inc</span></div>
  </section>

  <section class="card card-back" aria-label="Card back">
    <svg class="back-arc" viewBox="0 0 760 434" aria-hidden="true">
      <circle cx="672" cy="130" r="300" fill="var(--sun)"/>
      <circle cx="686" cy="126" r="294" fill="var(--paper)"/>
    </svg>
    <div class="brand"><span class="brand-dot"></span><span>Marlowe Crest Realty, Inc</span></div>

    <div class="person">
      <p class="person-name">GARY WHITLOCK</p>
      <p class="person-title">CEO/Managing Director</p>
    </div>

    <ul class="contacts">
      <li><svg viewBox="0 0 24 24"><path d="M5 3l4 1 1 5-2 1c1 3 3 5 6 6l1-2 5 1 1 4c-1 2-3 2-5 2C10 21 3 14 3 8c0-2 0-4 2-5z"/></svg>954-327-8846</li>
      <li><svg viewBox="0 0 24 24"><rect x="6" y="3" width="12" height="6"/><rect x="3" y="9" width="18" height="8" rx="1"/><rect x="7" y="14" width="10" height="7"/></svg>954-327-8846</li>
      <li><svg viewBox="0 0 24 24"><rect x="3" y="6" width="18" height="12"/><path d="M3 6l9 7 9-7"/></svg>garyshomes@quellmail.com</li>
      <li><svg viewBox="0 0 24 24"><circle cx="12" cy="12" r="9"/><ellipse cx="12" cy="12" rx="4" ry="9"/><path d="M3 12h18M5 7h14M5 17h14"/></svg>www.DwellTarrowBay.com</li>
      <li><svg viewBox="0 0 24 24"><path d="M12 22s-7-7-7-12a7 7 0 0 1 14 0c0 5-7 12-7 12z"/><circle cx="12" cy="10" r="2.5"/></svg><span>738 West Pinecrest Ave, Suite 410/510<br>Fort Lauderdale, FL 33308</span></li>
    </ul>
  </section>
</main>
</body>
</html>
```